Psychologist Banner Ads for Remarketing & chatterly

Brand awareness campaign for tealorchard.com.au

// Ad Formats //
Static JPEG
Max 45KB in file size
All ads must have a border

// Ad Sizes //
Static: (for Vantor Display network) 300×250, 160×600, 728×90
Static: (for Chatterly, no more than 25% text): 600×315, 1200 x 627

Please use logo, image and "maximise your wellbeing" from the website home page.

```html
<!DOCTYPE html>
<html lang="en">
<head>
<meta charset="utf-8">
<title>Teal Orchard Psychology – Banners for web ad</title>
<link href="https://fonts.googleapis.com/css2?family=Mulish:wght@400;600;700&display=swap" rel="stylesheet">
<style>
  :root {
    --board: #3d2416;
    --white: #ffffff;
    --sky-top: #d4e8f3;
    --sky-mid: #e6f1f8;
    --sky-low: #f3f8fb;
    --panel-blue: #d6eaf5;
    --ink-blue: #2a4f9f;
    --brand-blue: #2b5aa6;
    --button-blue: #213f94;
    --skin: #d7a98a;
    --hair: #6b4634;
  }
  * { box-sizing: border-box; margin: 0; padding: 0; }
  html, body {
    width: 1200px; height: 850px; overflow: hidden;
    background: var(--board);
    font-family: "Mulish", Arial, sans-serif;
  }
  .board { position: relative; width: 1200px; height: 850px; }

  .size-label, .board-title {
    position: absolute; color: var(--white); font-weight: 400;
  }
  .size-label { font-size: 24px; }
  .board-title { font-size: 46px; left: 678px; top: 166px; letter-spacing: 0.5px; }

  .banner { position: absolute; background: var(--white); overflow: hidden; }
  .banner > * { position: absolute; }

  .sky {
    background: linear-gradient(180deg, var(--sky-top) 0%, var(--sky-mid) 55%, var(--sky-low) 100%);
  }
  .sky-wide {
    background: linear-gradient(90deg, var(--sky-top) 0%, var(--sky-mid) 50%, var(--sky-low) 100%);
  }
  .photo-person {
    background: radial-gradient(ellipse at 45% 40%, var(--skin) 0%, #e8c9b2 30%, rgba(240,244,247,0.9) 62%, rgba(240,244,247,0) 80%);
  }
  .tagline {
    color: var(--ink-blue); font-weight: 400; text-align: center; letter-spacing: 1.5px;
  }
  .brand-name {
    color: var(--brand-blue); font-weight: 400; line-height: 1;
  }
  .brand-name .brand-line { display: block; }
  .brand-name .brand-sub { letter-spacing: 2px; }
  .action-panel { background: var(--panel-blue); }
  .visit-button {
    background: var(--button-blue); color: var(--white);
    display: flex; align-items: center; justify-content: center;
    font-weight: 400; letter-spacing: 2px;
  }
  .site-url { color: var(--button-blue); font-weight: 700; text-align: center; }

  /* 160x600 skyscraper */
  .skyscraper { left: 46px; top: 67px; width: 194px; height: 726px; }
  .skyscraper .sky { left: 6px; top: 6px; width: 182px; height: 430px; }
  .skyscraper .photo-person { left: 6px; top: 190px; width: 182px; height: 246px; }
  .skyscraper .tagline { left: 6px; top: 56px; width: 182px; font-size: 27px; line-height: 34px; }
  .skyscraper .brand-name { left: 14px; top: 458px; }
  .skyscraper .brand-line { font-size: 34px; line-height: 34px; }
  .skyscraper .brand-sub { font-size: 15px; margin-top: 6px; }
  .skyscraper .action-panel { left: 6px; top: 590px; width: 182px; height: 130px; }
  .skyscraper .visit-button { left: 27px; top: 630px; width: 137px; height: 38px; font-size: 26px; }
  .skyscraper .site-url { left: 6px; top: 676px; width: 182px; font-size: 14px; }

  /* 300x250 rectangle */
  .rectangle { left: 263px; top: 359px; width: 363px; height: 303px; }
  .rectangle .sky { left: 6px; top: 6px; width: 351px; height: 191px; }
  .rectangle .photo-person { left: 140px; top: 6px; width: 217px; height: 191px; }
  .rectangle .tagline { left: 16px; top: 100px; width: 135px; font-size: 21px; line-height: 25px; }
  .rectangle .brand-name { left: 26px; top: 208px; }
  .rectangle .brand-line { font-size: 27px; line-height: 28px; }
  .rectangle .brand-sub { font-size: 12px; margin-top: 4px; }
  .rectangle .visit-button { left: 226px; top: 220px; width: 92px; height: 38px; font-size: 22px; }
  .rectangle .site-url { left: 200px; top: 266px; width: 144px; font-size: 12px; }

  /* 728x90 leaderboard */
  .leaderboard { left: 255px; top: 680px; width: 882px; height: 108px; }
  .leaderboard .sky-wide { left: 6px; top: 6px; width: 589px; height: 96px; }
  .leaderboard .photo-person { left: 170px; top: 6px; width: 425px; height: 96px; }
  .leaderboard .tagline { left: 14px; top: 12px; width: 130px; font-size: 20px; line-height: 27px; }
  .leaderboard .brand-name { left: 608px; top: 18px; }
  .leaderboard .brand-line { font-size: 25px; line-height: 26px; }
  .leaderboard .brand-sub { font-size: 11px; margin-top: 4px; }
  .leaderboard .action-panel { left: 743px; top: 6px; width: 133px; height: 96px; }
  .leaderboard .visit-button { left: 772px; top: 34px; width: 74px; height: 32px; font-size: 19px; }
  .leaderboard .site-url { left: 743px; top: 72px; width: 133px; font-size: 11px; }
</style>
</head>
<body>
<main class="board">

  <section class="banner skyscraper" aria-label="160x600 banner">
    <div class="sky"></div>
    <div class="photo-person" role="img" aria-label="Photo of a smiling woman in a white top with arms raised against a pale sky"></div>
    <p class="tagline">maximise<br>your<br>wellbeing</p>
    <p class="brand-name"><span class="brand-line">Teal</span><span class="brand-line">Orchard</span><span class="brand-line brand-sub">PSYCHOLOGY</span></p>
    <div class="action-panel"></div>
    <div class="visit-button">VISIT</div>
    <p class="site-url">tealorchard.com.au</p>
  </section>
  <span class="size-label" style="left:254px; top:70px;">160x600</span>

  <h1 class="board-title">Banners for web ad</h1>

  <section class="banner rectangle" aria-label="300x250 banner">
    <div class="sky"></div>
    <div class="photo-person" role="img" aria-label="Photo of a smiling woman in a white top with arms raised against a pale sky"></div>
    <p class="tagline">maximise<br>your<br>wellbeing</p>
    <p class="brand-name"><span class="brand-line">Teal</span><span class="brand-line">Orchard</span><span class="brand-line brand-sub">PSYCHOLOGY</span></p>
    <div class="visit-button">VISIT</div>
    <p class="site-url">tealorchard.com.au</p>
  </section>
  <span class="size-label" style="left:507px; top:322px;">300x250</span>

  <section class="banner leaderboard" aria-label="728x90 banner">
    <div class="sky-wide"></div>
    <div class="photo-person" role="img" aria-label="Photo of a smiling woman in a white top with arms stretched wide against a pale sky"></div>
    <p class="tagline">maximise<br>your<br>wellbeing</p>
    <p class="brand-name"><span class="brand-line">Teal</span><span class="brand-line">Orchard</span><span class="brand-line brand-sub">PSYCHOLOGY</span></p>
    <div class="action-panel"></div>
    <div class="visit-button">VISIT</div>
    <p class="site-url">tealorchard.com.au</p>
  </section>
  <span class="size-label" style="left:1034px; top:638px;">728x90</span>

</main>
</body>
</html>
```